Quillmarsh Property Solutions need a business card design

Hello guys. We would need a business card design asap please.
We are a start up property investment business based in London UK specialised in buying, selling, managing and letting properties and helping distressed property owners.
The name of our Business is Quillmarsh, the logo symbolises the four fundamental elements of the world (earth, air, fire and water) and so it stands for strength, stability, longevity.
We would like the business card to communicate professionalism and reliability. Many many thanks indeed for your work.

Details:

1.) Rosalind Updike
Property Investor
Mobile: +44(0)7700123456
Email: rosalind.quillmarsh@mailbox-example.com

2.) Dominic Updike
Property Investor
Mobile: +44(0)7700987654
Email: dominic.quillmarsh@mailbox-example.com

```html
<!DOCTYPE html>
<html lang="en">
<head>
<meta charset="utf-8">
<title>Quillmarsh Property Solutions — Business Card</title>
<link rel="stylesheet" href="https://fonts.googleapis.com/css2?family=Montserrat:wght@800&family=Open+Sans:wght@400;600&display=swap">
<style>
  :root {
    --page: #e9e6e1;
    --card-white: #ffffff;
    --brand-green: #175a2e;
    --accent-red: #c8202f;
    --accent-blue: #27489a;
    --ink: #1d1d1f;
    --ink-soft: #555a5e;
    --divider: #c9c9c9;
  }
  * { box-sizing: border-box; margin: 0; padding: 0; }
  html, body { width: 1200px; height: 720px; overflow: hidden; }
  body {
    background: var(--page);
    font-family: "Open Sans", Arial, sans-serif;
    position: relative;
  }
  .card {
    position: absolute;
    width: 560px;
    height: 320px;
    top: 200px;
    overflow: hidden;
    box-shadow: 0 6px 18px rgba(0,0,0,0.18);
  }
  .card--front { left: 30px; background: var(--card-white); }
  .card--back { left: 610px; background: var(--brand-green); }

  .card__waves { position: absolute; inset: 0; width: 100%; height: 100%; }

  .brand {
    position: absolute;
    left: 80px;
    top: 112px;
    display: flex;
    align-items: center;
    gap: 10px;
  }
  .brand__mark {
    width: 14px;
    height: 14px;
    background: var(--brand-green);
  }
  .brand__text {
    font-family: "Montserrat", Arial, sans-serif;
    font-weight: 800;
    color: var(--ink);
    line-height: 1.1;
  }
  .brand__name { font-size: 21px; letter-spacing: 0.5px; }
  .brand__tagline { font-size: 8.5px; letter-spacing: 1.6px; }

  .divider {
    position: absolute;
    left: 276px;
    top: 62px;
    width: 1px;
    height: 78px;
    background: linear-gradient(var(--divider), transparent);
  }

  .contact {
    position: absolute;
    left: 290px;
    top: 66px;
    list-style: none;
    font-size: 12px;
    color: var(--ink-soft);
  }
  .contact__item {
    display: flex;
    align-items: center;
    gap: 8px;
    margin-bottom: 10px;
  }
  .contact__icon { width: 11px; height: 11px; fill: var(--ink-soft); }

  .person {
    position: absolute;
    right: 24px;
    top: 196px;
    text-align: right;
    color: var(--card-white);
    line-height: 1.3;
  }
  .person__name { font-weight: 600; font-size: 15px; }
  .person__role { font-size: 11px; }

  .back-brand {
    position: absolute;
    inset: 0;
    display: flex;
    align-items: center;
    justify-content: center;
    gap: 14px;
  }
  .back-brand__mark { width: 22px; height: 22px; background: var(--card-white); }
  .back-brand__name {
    font-family: "Montserrat", Arial, sans-serif;
    font-weight: 800;
    font-size: 40px;
    letter-spacing: 1px;
    color: var(--card-white);
  }
</style>
</head>
<body>

<section class="card card--front" aria-label="Business card front">
  <svg class="card__waves" viewBox="0 0 560 320" preserveAspectRatio="none" aria-hidden="true">
    <path d="M0,0 L0,150 C10,90 40,40 95,0 Z" fill="var(--brand-green)"/>
    <path d="M0,160 C12,95 45,42 105,0" fill="none" stroke="var(--accent-red)" stroke-width="3"/>
    <path d="M0,172 C15,105 52,48 118,0" fill="none" stroke="var(--accent-blue)" stroke-width="1.5"/>
    <path d="M0,320 L0,292 C140,304 260,252 360,202 C430,168 500,160 560,156 L560,320 Z" fill="var(--brand-green)"/>
    <path d="M0,280 C140,292 260,240 360,190 C430,156 500,148 560,144" fill="none" stroke="var(--accent-red)" stroke-width="3"/>
    <path d="M0,272 C140,284 260,232 360,182 C430,148 500,140 560,136" fill="none" stroke="var(--accent-blue)" stroke-width="1.5"/>
  </svg>

  <div class="brand">
    <span class="brand__mark"></span>
    <div class="brand__text">
      <div class="brand__name">QUILLMARSH</div>
      <div class="brand__tagline">PROPERTY SOLUTIONS</div>
    </div>
  </div>

  <div class="divider"></div>

  <ul class="contact">
    <li class="contact__item">
      <svg class="contact__icon" viewBox="0 0 12 12" aria-hidden="true"><rect x="3" y="0" width="6" height="12" rx="1.2"/></svg>
      <span>+44(0)7700987654</span>
    </li>
    <li class="contact__item">
      <svg class="contact__icon" viewBox="0 0 12 12" aria-hidden="true"><path d="M0,2 H12 V10 H0 Z M0,2 L6,7 L12,2" fill="none" stroke="var(--ink-soft)" stroke-width="1.4"/></svg>
      <span>dominic.quillmarsh@mailbox-example.com</span>
    </li>
  </ul>

  <div class="person">
    <div class="person__name">Dominic Updike</div>
    <div class="person__role">Property Investor</div>
  </div>
</section>

<section class="card card--back" aria-label="Business card back">
  <div class="back-brand">
    <span class="back-brand__mark"></span>
    <span class="back-brand__name">QUILLMARSH</span>
  </div>
</section>

</body>
</html>
```